Brightmoor Talent company

We require a website for job recruitment company called "Brightmoor Talent"
Our company is specialising in recruitment of skilled labour from Sri Lanka into Australian market.
We would like to include a job advertising plugin where jobs can be listed and applied for .
COPYWRITING MUST BE INCLUDED !

Industry/Entity Type

Recruitment

Coding

Coded - Design and coding required

Number of Pages Required

5+ page

Colors

Designer to choose colors to be used in the design.

```html
<!DOCTYPE html>
<html lang="en">
<head>
<meta charset="utf-8">
<title>Brightmoor Talent – Skilled Recruitment</title>
<link href="https://fonts.googleapis.com/css2?family=Playfair+Display:wght@700;800&family=Roboto:wght@400;500;700&display=swap" rel="stylesheet">
<style>
:root{
  --blue:#0b4f9f;
  --blue-dark:#083d7c;
  --orange:#e4411a;
  --ink:#1b1b1b;
  --body:#555b63;
  --muted:#8a9099;
  --pale:#eef2f7;
  --footer:#161616;
  --white:#ffffff;
  --star:#f5a623;
}
*{box-sizing:border-box;margin:0;padding:0}
html,body{width:1200px;height:3958px;overflow:hidden}
body{position:relative;font-family:'Roboto',sans-serif;color:var(--body);background:var(--white)}
.abs{position:absolute}
.serif{font-family:'Playfair Display',serif}
.btn{position:absolute;display:flex;align-items:center;justify-content:center;gap:9px;border-radius:20px;color:var(--white);font:700 13px 'Roboto',sans-serif;text-transform:uppercase;letter-spacing:.2px}
.btn-blue{background:var(--blue)}
.btn-orange{background:var(--orange)}
.btn .dot{width:12px;height:12px;border-radius:50%;background:var(--white);position:relative}
.btn .dot::after{content:"";position:absolute;left:4px;top:3px;border-left:5px solid currentColor;border-top:3px solid transparent;border-bottom:3px solid transparent}
.btn-blue .dot::after{border-left-color:var(--blue)}
.btn-orange .dot::after{border-left-color:var(--orange)}
.section-title{position:absolute;left:0;width:1200px;text-align:center;font:700 31px 'Playfair Display',serif;color:var(--ink);text-transform:uppercase}
.section-title span{color:var(--blue)}

/* header */
.topline{left:0;top:0;width:1200px;height:4px;background:var(--blue)}
.header{left:0;top:4px;width:1200px;height:70px;background:var(--white)}
.logo-box{left:111px;top:0;width:181px;height:94px;background:var(--white);z-index:3;display:flex;flex-direction:column;align-items:center;justify-content:center;font:700 24px/1.05 'Playfair Display',serif;color:var(--blue)}
.nav{left:426px;top:30px;display:flex;gap:0;font-size:15px;color:#222}
.nav a{position:absolute;white-space:nowrap;text-decoration:none;color:#222}
.nav a.active{color:var(--blue);border-bottom:2px solid var(--blue);padding-bottom:4px}
.social{width:30px;height:30px;border-radius:50%;background:var(--blue)}

/* hero */
.hero{left:0;top:74px;width:1200px;height:694px;background:linear-gradient(100deg,#6d5b4a 0%,#a8917a 25%,#d9d0c4 40%,#5a4a3e 60%,#3a2f28 80%,#2b231e 100%)}
.hero-title{left:665px;color:var(--white)}
.hero-welcome{top:296px;font:700 31px 'Playfair Display',serif}
.hero-name{top:340px;font:700 56px 'Playfair Display',serif;white-space:nowrap}
.hero-text{top:428px;width:420px;font-size:15px;line-height:22px;color:#f1eee9}

/* about */
.about-title{left:114px;top:888px;font:700 31px 'Playfair Display',serif;color:var(--ink)}
.about-title span{color:var(--blue)}
.about-text{left:114px;top:935px;width:470px;font-size:15.5px;line-height:25.7px;text-align:justify;color:#4d525a}
.about-photo{left:655px;top:857px;width:430px;height:430px;border-radius:50%;border:5px solid var(--blue);background:radial-gradient(circle at 65% 45%,#8a6a52 0%,#b7a48f 30%,#d8d3c8 60%,#8f9a8d 100%)}

/* jobs */
.jobs{left:0;top:1368px;width:1200px;height:632px;background:var(--pale)}
.job-card{position:absolute;top:1518px;width:307px;height:409px;background:var(--white);box-shadow:0 4px 14px rgba(0,0,0,.06);text-align:center}
.job-img{position:absolute;left:6px;top:6px;width:295px;height:189px}
.job-card h3{position:absolute;left:0;top:216px;width:100%;font:500 17px 'Roboto',sans-serif;color:var(--ink)}
.job-card .rule{position:absolute;left:139px;top:248px;width:29px;height:2px;background:var(--blue)}
.job-card p{position:absolute;left:22px;top:262px;width:263px;font-size:13px;line-height:21px;color:var(--muted)}
.arrow-btn{position:absolute;top:1705px;width:35px;height:35px;border-radius:50%;background:var(--white);border:1px solid #dde2e8}

/* testimonials */
.t-card{position:absolute;top:2167px;width:392px;height:230px}
.t-card::before{content:"";position:absolute;inset:0;background:var(--white);border-radius:42px;transform:skewX(-5deg);box-shadow:0 6px 22px rgba(0,0,0,.08)}
.t-avatar{position:absolute;width:114px;height:114px;border-radius:50%;top:2226px;background:linear-gradient(135deg,#9aa8b6,#4d5d6e)}
.t-body{position:absolute;top:2200px;width:270px}
.t-quote{font:800 52px/40px 'Playfair Display',serif;color:var(--blue);height:40px}
.t-text{margin-top:12px;font-size:14px;line-height:24px;color:var(--muted)}
.t-name{margin-top:14px;font:500 16px 'Roboto',sans-serif;color:var(--ink)}
.t-stars{margin-top:8px;display:flex;gap:3px}

/* contact */
.contact{left:0;top:2483px;width:1200px;height:538px;background:linear-gradient(120deg,#0c4d9c 0%,#165aa8 40%,#0b4a95 70%,#0e52a2 100%)}
.contact-title{color:var(--white)}
.field{position:absolute;background:var(--white);border-radius:22px;display:flex;align-items:center;gap:12px;padding-left:28px;font-size:13px;color:#333}
.field svg{flex:none}

/* news */
.news-img{position:absolute;top:3170px;width:310px;height:211px}
.news-date{position:absolute;top:3190px;width:43px;height:43px;background:var(--orange);color:var(--white);border-radius:4px;text-align:center;font:500 13px/17px 'Roboto',sans-serif;padding-top:4px}
.news-box{position:absolute;top:3362px;width:292px;height:137px;background:var(--white);box-shadow:0 4px 14px rgba(0,0,0,.1);padding:20px 24px}
.news-cat{display:flex;align-items:center;gap:7px;font-size:12px;color:var(--muted)}
.news-box h4{margin-top:10px;font:500 16.5px/24px 'Roboto',sans-serif;color:var(--ink)}
.news-meta{margin-top:10px;display:flex;gap:18px;font-size:12px;color:var(--muted)}
.news-meta span{display:flex;align-items:center;gap:7px}

/* footer */
.footer{left:0;top:3575px;width:1200px;height:338px;background:var(--footer)}
.f-logo{left:124px;top:3668px;width:200px;text-align:center;font:700 33px/1.05 'Playfair Display',serif;color:var(--white)}
.f-social{position:absolute;top:3774px;width:30px;height:30px;border-radius:50%;border:1.5px solid var(--white)}
.f-col{position:absolute;color:var(--white)}
.f-col h5{font:700 17px 'Roboto',sans-serif;margin-bottom:16px}
.f-col li{list-style:none;font-size:15px;line-height:31px}
.f-contact{position:absolute;left:900px;color:var(--white);font-size:13.5px}
.f-contact .lbl{font:700 12px 'Roboto',sans-serif;margin-bottom:5px}
.f-contact .row{display:flex;gap:10px}
.bottom-bar{left:0;top:3913px;width:1200px;height:45px;background:var(--blue);color:var(--white);font-size:14px;display:flex;align-items:center;justify-content:center}
</style>
</head>
<body>

<!-- header -->
<div class="abs topline"></div>
<header class="abs header"></header>
<div class="abs logo-box"><span>Brightmoor</span><span>Talent</span></div>
<nav class="abs nav" style="left:0;top:32px;width:1200px;height:30px">
  <a class="active" style="left:426px">HOME</a>
  <a style="left:496px">JOBS</a>
  <a style="left:561px">SERVICES</a>
  <a style="left:656px">ABOUT US</a>
  <a style="left:755px">NEWS</a>
  <a style="left:825px">CONTACT US</a>
</nav>
<div class="abs social" style="left:950px;top:24px" aria-label="Social link"></div>
<div class="abs social" style="left:985px;top:24px" aria-label="Social link"></div>
<div class="abs social" style="left:1021px;top:24px" aria-label="Social link"></div>
<div class="abs social" style="left:1056px;top:24px" aria-label="Social link"></div>

<!-- hero -->
<section class="abs hero" role="img" aria-label="Photo of a smiling candidate handing over her resume at a job interview"></section>
<div class="abs hero-title hero-welcome">Welcome To</div>
<h1 class="abs hero-title hero-name">Brightmoor Talent</h1>
<p class="abs hero-title hero-text">Lorem ipsum dolor sit amet, consectetur adipiscing elitsed do eiusmod tempor incididunt ut labore et dolore magna.</p>
<a class="btn btn-blue" style="left:667px;top:498px;width:149px;height:40px">Get Started <i class="dot"></i></a>
<a class="btn btn-orange" style="left:830px;top:498px;width:149px;height:40px">Register Now <i class="dot"></i></a>

<!-- about -->
<h2 class="abs about-title">About <span>Us</span></h2>
<p class="abs about-text">Lorem ipsum dolor sit amet, consectetur adipiscing elit, sed do eiusmod tempor incididunt ut labore et dolore magna aliqua. Ut enim ad minim veniam, quis nostrud exercitation ullamco laboris nisi ut aliquip ex ea commodo consequat. Duis aute irure dolor in reprehenderit in voluptate velit esse cillum dolore eu fugiat nulla pariatur. Excepteur sint occaecat cupidatat non proident, sunt in culpa qui officia deserunt mollit anim id est laborum Sed ut perspiciatis unde omnis iste natus error sit voluptatem accusantium doloremque laudantium, totam rem aperiam, eaque ipsa quae ab illo inventoresint occaecat cupidatat non proident, sunt ined.</p>
<a class="btn btn-blue" style="left:114px;top:1209px;width:149px;height:40px">Learn More <i class="dot"></i></a>
<div class="abs about-photo" role="img" aria-label="Photo of a recruiter interviewing a smiling candidate in an office"></div>

<!-- jobs -->
<section class="abs jobs"></section>
<h2 class="section-title" style="top:1434px">Job <span>Openings</span></h2>
<div class="arrow-btn" style="left:36px"><svg width="35" height="35" viewBox="0 0 35 35"><path d="M19.5 12l-5 5.5 5 5.5" fill="none" stroke="#777" stroke-width="1.5"/></svg></div>
<div class="arrow-btn" style="left:1128px"><svg width="35" height="35" viewBox="0 0 35 35"><path d="M15.5 12l5 5.5-5 5.5" fill="none" stroke="#777" stroke-width="1.5"/></svg></div>

<article class="job-card" style="left:111px">
  <div class="job-img" role="img" aria-label="Photo of two mechanics working in a workshop" style="background:linear-gradient(135deg,#3b3f44,#6f7378 50%,#2d2f33)"></div>
  <h3>Lorem ipsum dolor sit amet</h3><i class="rule"></i>
  <p>Lorem ipsum &nbsp;consectetur adipiscingelit sed &nbsp;eiusmod temporincidid untutlabore dolored magnasd aliquad Uted enim.</p>
  <a class="btn btn-orange" style="left:92px;top:349px;width:123px;height:34px;font-size:11.5px">Apply Now <i class="dot"></i></a>
</article>
<article class="job-card" style="left:446px">
  <div class="job-img" role="img" aria-label="Photo of two engineers in hard hats on a factory floor" style="background:linear-gradient(135deg,#c9ccd0,#7a8088 50%,#3f454c)"></div>
  <h3>Lorem ipsum dolor sit amet</h3><i class="rule"></i>
  <p>Lorem ipsum &nbsp;consectetur adipiscingelit sed &nbsp;eiusmod temporincidid untutlabore dolored magnasd aliquad Uted enim.</p>
  <a class="btn btn-blue" style="left:92px;top:349px;width:123px;height:34px;font-size:11.5px">Apply Now <i class="dot"></i></a>
</article>
<article class="job-card" style="left:780px">
  <div class="job-img" role="img" aria-label="Photo of a young woman working on a laptop" style="background:linear-gradient(135deg,#7a4a2a,#b07a4a 45%,#e0b24a 75%,#d8d2c8)"></div>
  <h3>Lorem ipsum dolor sit amet</h3><i class="rule"></i>
  <p>Lorem ipsum &nbsp;consectetur adipiscingelit sed &nbsp;eiusmod temporincidid untutlabore dolored magnasd aliquad Uted enim.</p>
  <a class="btn btn-orange" style="left:92px;top:349px;width:123px;height:34px;font-size:11.5px">Apply Now <i class="dot"></i></a>
</article>

<!-- testimonials -->
<h2 class="section-title" style="top:2080px">What Our <span>Clients Say</span></h2>

<div class="t-card" style="left:181px"></div>
<div class="t-avatar" style="left:132px" role="img" aria-label="Portrait photo of a client"></div>
<div class="t-body" style="left:276px">
  <div class="t-quote">&ldquo;</div>
  <p class="t-text">Lorem ipsum dolor sit amet, consectetur adipiscing elit, sed do eiusmod tempor ut labore et dolore magna aliqua.</p>
  <div class="t-name">Marcus T</div>
  <div class="t-stars"><svg width="96" height="16" viewBox="0 0 96 16" fill="#f5a623"><g id="st"><path d="M8 1l2 4.6 5 .4-3.8 3.3 1.2 4.9L8 11.6 3.6 14.2l1.2-4.9L1 6l5-.4z"/></g><use href="#st" x="19"/><use href="#st" x="38"/><use href="#st" x="57"/><use href="#st" x="76"/></svg></div>
</div>

<div class="t-card" style="left:668px"></div>
<div class="t-avatar" style="left:619px" role="img" aria-label="Portrait photo of a client"></div>
<div class="t-body" style="left:764px">
  <div class="t-quote">&ldquo;</div>
  <p class="t-text">Lorem ipsum dolor sit amet, consectetur adipiscing elit, sed do eiusmod tempor ut labore et dolore magna aliqua.</p>
  <div class="t-name">Marcus T</div>
  <div class="t-stars"><svg width="96" height="16" viewBox="0 0 96 16" fill="#f5a623"><use href="#st"/><use href="#st" x="19"/><use href="#st" x="38"/><use href="#st" x="57"/><use href="#st" x="76"/></svg></div>
</div>

<!-- contact -->
<section class="abs contact" role="img" aria-label="Blue tinted photo of an office team at work"></section>
<h2 class="section-title contact-title" style="top:2544px">Get In Touch</h2>
<div class="field" style="left:157px;top:2621px;width:439px;height:45px"><svg width="12" height="12" viewBox="0 0 12 12" fill="#222"><circle cx="6" cy="3.3" r="2.8"/><path d="M0.5 12c0-3.5 2.5-5 5.5-5s5.5 1.5 5.5 5z"/></svg>First Name</div>
<div class="field" style="left:604px;top:2621px;width:438px;height:45px"><svg width="12" height="12" viewBox="0 0 12 12" fill="#222"><circle cx="6" cy="3.3" r="2.8"/><path d="M0.5 12c0-3.5 2.5-5 5.5-5s5.5 1.5 5.5 5z"/></svg>Last Name</div>
<div class="field" style="left:157px;top:2684px;width:439px;height:45px"><svg width="13" height="10" viewBox="0 0 13 10"><rect width="13" height="10" rx="1" fill="#222"/><path d="M1 1.5l5.5 4 5.5-4" fill="none" stroke="#fff" stroke-width="1"/></svg>Email</div>
<div class="field" style="left:604px;top:2684px;width:438px;height:45px"><svg width="8" height="12" viewBox="0 0 8 12"><rect x=".7" y=".7" width="6.6" height="10.6" rx="1.2" fill="none" stroke="#222" stroke-width="1.4"/></svg>Phone</div>
<div class="field" style="left:157px;top:2749px;width:885px;height:118px;align-items:flex-start;padding-top:22px;padding-left:34px"><svg width="14" height="11" viewBox="0 0 14 11" fill="#222"><ellipse cx="5.5" cy="4" rx="5.5" ry="4"/><ellipse cx="9.5" cy="6.5" rx="4.5" ry="3.5"/></svg>Comments</div>
<a class="btn btn-orange" style="left:525px;top:2911px;width:149px;height:38px">Submit Now <i class="dot"></i></a>

<!-- news -->
<h2 class="section-title" style="top:3095px">Latest <span>News</span></h2>

<div class="news-img" style="left:111px;background:linear-gradient(135deg,#3a3a3c,#c9c3bb 45%,#e8e4dd 70%,#4a4b4e)" role="img" aria-label="Photo of colleagues reviewing documents in a meeting"></div>
<div class="news-date" style="left:360px">Nov<br>11</div>
<div class="news-box" style="left:129px">
  <div class="news-cat"><svg width="8" height="11" viewBox="0 0 8 11"><path d="M4 0a4 4 0 0 1 4 4c0 3-4 7-4 7S0 7 0 4a4 4 0 0 1 4-4z" fill="#e4411a"/><circle cx="4" cy="4" r="1.5" fill="#fff"/></svg>Lorem ipsum dolor</div>
  <h4>Lorem ipsum dolor sit amet sed conseum dolor sictea.</h4>
  <div class="news-meta"><span><svg width="10" height="11" viewBox="0 0 12 12" fill="#e4411a"><circle cx="6" cy="3.3" r="2.8"/><path d="M0.5 12c0-3.5 2.5-5 5.5-5s5.5 1.5 5.5 5z"/></svg>John Doe</span><span><svg width="13" height="10" viewBox="0 0 14 11" fill="#e4411a"><ellipse cx="5.5" cy="4" rx="5.5" ry="4"/><ellipse cx="9.5" cy="6.5" rx="4.5" ry="3.5"/></svg>0 Comments</span></div>
</div>

<div class="news-img" style="left:446px;background:linear-gradient(135deg,#6b5a4a,#d8d0c4 40%,#f1eee8 60%,#3e3a36)" role="img" aria-label="Photo of a candidate smiling during an interview"></div>
<div class="news-date" style="left:695px">Nov<br>11</div>
<div class="news-box" style="left:464px">
  <div class="news-cat"><svg width="8" height="11" viewBox="0 0 8 11"><path d="M4 0a4 4 0 0 1 4 4c0 3-4 7-4 7S0 7 0 4a4 4 0 0 1 4-4z" fill="#e4411a"/><circle cx="4" cy="4" r="1.5" fill="#fff"/></svg>Lorem ipsum dolor</div>
  <h4>Lorem ipsum dolor sit amet sed conseum dolor sictea.</h4>
  <div class="news-meta"><span><svg width="10" height="11" viewBox="0 0 12 12" fill="#e4411a"><circle cx="6" cy="3.3" r="2.8"/><path d="M0.5 12c0-3.5 2.5-5 5.5-5s5.5 1.5 5.5 5z"/></svg>John Doe</span><span><svg width="13" height="10" viewBox="0 0 14 11" fill="#e4411a"><ellipse cx="5.5" cy="4" rx="5.5" ry="4"/><ellipse cx="9.5" cy="6.5" rx="4.5" ry="3.5"/></svg>0 Comments</span></div>
</div>

<div class="news-img" style="left:780px;background:linear-gradient(135deg,#f3f1ee,#c8bcb0 40%,#4a3a30 60%,#e9e6e1)" role="img" aria-label="Photo of a candidate shaking hands at an interview"></div>
<div class="news-date" style="left:1029px">Nov<br>11</div>
<div class="news-box" style="left:798px">
  <div class="news-cat"><svg width="8" height="11" viewBox="0 0 8 11"><path d="M4 0a4 4 0 0 1 4 4c0 3-4 7-4 7S0 7 0 4a4 4 0 0 1 4-4z" fill="#e4411a"/><circle cx="4" cy="4" r="1.5" fill="#fff"/></svg>Lorem ipsum dolor</div>
  <h4>Lorem ipsum dolor sit amet sed conseum dolor sictea.</h4>
  <div class="news-meta"><span><svg width="10" height="11" viewBox="0 0 12 12" fill="#e4411a"><circle cx="6" cy="3.3" r="2.8"/><path d="M0.5 12c0-3.5 2.5-5 5.5-5s5.5 1.5 5.5 5z"/></svg>John Doe</span><span><svg width="13" height="10" viewBox="0 0 14 11" fill="#e4411a"><ellipse cx="5.5" cy="4" rx="5.5" ry="4"/><ellipse cx="9.5" cy="6.5" rx="4.5" ry="3.5"/></svg>0 Comments</span></div>
</div>

<!-- footer -->
<footer class="abs footer"></footer>
<div class="abs f-logo">Brightmoor<br>Talent</div>
<div class="f-social" style="left:148px" aria-label="Social link"></div>
<div class="f-social" style="left:189px" aria-label="Social link"></div>
<div class="f-social" style="left:229px" aria-label="Social link"></div>
<div class="f-social" style="left:271px" aria-label="Social link"></div>

<div class="f-col" style="left:444px;top:3641px">
  <h5>Quick links</h5>
  <ul><li>Home</li><li>Jobs</li><li>Services</li><li>About Us</li><li>Latest News</li><li>Contact Us</li></ul>
</div>
<div class="f-col" style="left:656px;top:3641px">
  <h5>About Company</h5>
  <ul><li>Legal Information</li><li>Terms &amp; Condition</li><li>Privacy Policy</li><li>Support</li><li>Site Map</li></ul>
</div>
<div class="f-col" style="left:900px;top:3638px"><h5>Contact Us</h5></div>
<div class="f-contact" style="top:3682px">
  <div class="row"><svg width="12" height="12" viewBox="0 0 12 12"><path d="M2.5 0.5l2 2.5-1.2 1.5c.8 1.7 2.2 3.1 3.9 3.9L8.7 7.2l2.6 2-1 2.1C5.5 11.5.5 6.5.4 1.5z" fill="#2f7de1"/></svg><div><div class="lbl">Phone</div><div style="padding-left:14px">+1 555 010 2040</div></div></div>
</div>
<div class="f-contact" style="top:3733px">
  <div class="row"><svg width="13" height="10" viewBox="0 0 13 10"><rect width="13" height="10" rx="1" fill="#2f7de1"/><path d="M1 1.5l5.5 4 5.5-4" fill="none" stroke="#161616" stroke-width="1"/></svg><div><div class="lbl">Email</div><div>info@brightmoortalent.com</div></div></div>
</div>
<div class="f-contact" style="top:3785px">
  <div class="row"><svg width="9" height="12" viewBox="0 0 8 11"><path d="M4 0a4 4 0 0 1 4 4c0 3-4 7-4 7S0 7 0 4a4 4 0 0 1 4-4z" fill="#2f7de1"/><circle cx="4" cy="4" r="1.5" fill="#161616"/></svg><div><div class="lbl">Location</div><div style="padding-left:4px;line-height:18px">777 Lorem ipsum dolor sit<br>consectetur adipiscing elit,</div></div></div>
</div>

<div class="abs bottom-bar">2022 Copyright - Brightmoor Talent &nbsp;&nbsp;| &nbsp;&nbsp;All Rights Reserved</div>

</body>
</html>
```